K&T Smokehouse Website Design Project

K& T Smokehouse AsaderÃa is a fast-casual restaurant that specializes in southern culture, soul food, baby back ribs and bourbon whiskey.
We need a functional and user friendly website design for our customers to be able to explore our menu options, learn about our culture, as well as be able to place and pay for online orders that can be picked up at the nearest restaurant. Benchmarks for our website are www.crumbvalebakery.com, www.zestoragrill.com and www.marisolkitchen.com
The site design should also serve as an initial point of contact for prospective franchisees to dig and learn about the brand and business opportunity.
We want customers (consumers and potential franchisees) to be able to experience FIRST THE FOOD, but also the style and culture of our restaurants via the website design. Key elements for this are: soul food (Warm Your Heart), southern culture, friendly service, bluegrass/folk music, bourbon/moonshine/Tennessee whisky, modern butcher-shop design as well as industrial, wood, modern rustic, organic elements. (see restaurant images of tile, concrete, vintage scales, green wall, etc)
We want the website to provide a good overall brand image and also drive participation and sales by via images of our food, by these images being at front and center of the website design. See benchmark websites (Crumbvale, Marisol Kitchen, Zestora) for good examples of this.
Other elements to take under consideration for the website design are:
* Illustrative but simple menu
* Hacer un pedido (order online), Loyalty Program and Franquicias sections should have different, separate and easy to see buttons in the homepage.
* Simple, but modern functionality overall for the website.
* Respect colors and elements of the brand (attached some photos and examples)
* Brand Typography included (NAMES OF TYPOGRAPHY: BEBAS, SONGBIRD, CANTER & VAST SHADOW)
Minimum Deliverables: Home Page, Menu and Order Online. 3 pages total.
• More examples can be found at: www.facebook.com/ktsmokehouseasaderia
• Website architecture / Site Map ATTACHED
* More design elements attached.
* Screenshots of some good elements to take under consideration for website functionality and design.
- BEBAS, SONGBRID, CANTER & VAST SHADOW

```html
<!DOCTYPE html>
<html lang="es">
<head>
<meta charset="utf-8">
<title>K&amp;T Smokehouse Asadería</title>
<link rel="stylesheet" href="https://fonts.googleapis.com/css2?family=Montserrat:wght@400;500;600&family=Roboto:wght@400;500;700&family=Roboto+Condensed:wght@700&display=swap">
<style>
:root{
  --wine:#4f0606;
  --wine-deep:#3a0303;
  --ink:#111;
  --white:#fff;
  --accent:#f0a24b;
  --red-text:#8c0f0f;
  --grey:#666;
}
*{margin:0;padding:0;box-sizing:border-box}
html,body{width:700px;height:1200px;overflow:hidden;background:var(--white)}
body{position:relative;font-family:"Roboto",sans-serif;color:var(--ink)}
.abs{position:absolute}

/* hero */
.hero{left:0;top:0;width:700px;height:388px;background:radial-gradient(ellipse at 58% 55%,#3b1c10 0%,#2a140b 35%,#4a2a17 70%,#2d1a10 100%)}
.hero-photo{left:0;top:0;width:700px;height:388px;background:linear-gradient(120deg,rgba(200,190,170,.35) 0%,rgba(200,190,170,.15) 35%,rgba(0,0,0,0) 55%)}
.nav-item{top:30px;font-family:"Montserrat",sans-serif;font-size:7.6px;font-weight:500;color:var(--white);letter-spacing:-.1px;white-space:nowrap}
.nav-item.current{color:var(--accent)}
.brand{left:298px;top:6px;width:120px;height:76px;border-radius:50%;background:var(--ink);border:2px solid var(--white);display:flex;align-items:center;justify-content:center;text-align:center;font-family:"Montserrat",sans-serif;font-weight:600;font-size:11px;line-height:13px;color:var(--white)}
.btn-outline{top:19px;height:28px;border:1px solid rgba(255,255,255,.8);color:var(--white);font-family:"Montserrat",sans-serif;font-size:10px;font-weight:500;display:flex;align-items:center;justify-content:center;background:rgba(0,0,0,.25);white-space:nowrap}
.hero-title{left:58px;top:172px;font-family:"Roboto Condensed",sans-serif;font-weight:700;font-size:23.5px;line-height:32px;color:var(--white);letter-spacing:.2px;text-shadow:0 1px 3px rgba(0,0,0,.6)}
.btn-more{left:56px;top:254px;width:99px;height:35px;background:linear-gradient(#4a0505,#2b0202);color:var(--white);font-size:12.5px;display:flex;align-items:center;justify-content:center;box-shadow:0 2px 4px rgba(0,0,0,.5)}
.dots{left:670px;top:200px;display:flex;flex-direction:column;gap:6px}
.dots span{width:6px;height:6px;border-radius:50%;background:var(--white)}
.dots .on{background:#9b1a1a}

/* featured */
.featured{left:0;top:388px;width:700px;height:193px;background:var(--wine)}
.feature-card{top:35px;width:192px;height:130px;border:2px solid #e6e0dc}
.feature-card .photo{width:100%;height:100%}
.feature-card .label{position:absolute;left:0;bottom:0;width:100%;height:23px;background:rgba(40,40,40,.7);color:var(--white);font-family:"Montserrat",sans-serif;font-size:10.5px;font-weight:500;padding:6px 0 0 9px;white-space:nowrap}

/* menu */
.menu{left:0;top:581px;width:700px;height:277px;background:radial-gradient(ellipse at 50% 40%,#3a2418 0%,#221510 55%,#120b08 100%)}
.menu-title{left:0;top:32px;width:700px;text-align:center;font-family:"Montserrat",sans-serif;font-weight:600;font-size:17px;color:var(--white)}
.dish{top:65px;width:145px;height:159px;background:var(--white)}
.dish .photo{width:145px;height:84px}
.dish .name{margin-top:10px;text-align:center;font-size:8.5px;font-weight:500;color:var(--red-text)}
.dish .price{margin-top:5px;text-align:center;font-size:8.5px;color:#b01313}
.dish .order{margin:8px auto 0;width:68px;height:20px;background:#222;border-radius:2px;color:var(--white);font-size:7px;display:flex;align-items:center;justify-content:center}
.arrow{top:128px}

/* news & blog */
.section-title{font-family:"Montserrat",sans-serif;font-size:13px;font-weight:500;color:#222}
.news-item{left:48px;width:152px;height:40px}
.date{position:absolute;left:0;top:0;width:35px;height:36px;background:#f1f1f1;border:1px solid #ddd;text-align:center}
.date b{display:block;margin-top:5px;font-size:11px}
.date i{display:block;font-style:normal;font-size:6.5px;color:var(--grey);margin-top:4px}
.news-item h3{position:absolute;left:41px;top:2px;font-size:8px;font-weight:500;color:var(--red-text);white-space:nowrap}
.news-item p{position:absolute;left:41px;top:18px;font-size:7px;color:#333;white-space:nowrap}
.news-rule{left:52px;top:966px;width:146px;border-top:1px dotted #777}
.post{top:912px;width:133px;height:108px;background:var(--white);box-shadow:0 1px 3px rgba(0,0,0,.3)}
.post .photo{width:133px;height:76px}
.post p{text-align:center;margin-top:11px;font-size:7px;color:var(--red-text)}

/* contact */
.contact{left:0;top:1041px;width:700px;height:82px;background:var(--wine)}
.contact .loc{left:52px;top:34px;font-family:"Montserrat",sans-serif;font-size:13px;font-weight:400;color:var(--white)}
.select{left:156px;top:28px;width:170px;height:29px;background:var(--white);border:1px solid #bbb;font-size:7px;font-style:italic;color:#555;padding:10px 0 0 9px}
.delivery{left:398px;top:24px;color:var(--white);font-family:"Montserrat",sans-serif;font-size:10.5px;line-height:21px;white-space:nowrap}
.phone{left:533px;top:30px;display:flex;align-items:center;gap:7px;color:var(--white);font-size:18px;font-weight:500}

/* footer */
.footer{left:0;top:1123px;width:700px;height:77px;background:#070707;color:var(--white)}
.footer .links{left:54px;top:22px;font-size:7px;font-weight:400;color:var(--white)}
.footer .copy{left:53px;top:39px;font-size:7px;font-weight:400;color:var(--white)}
.follow{left:537px;top:24px;font-size:8.5px;font-family:"Montserrat",sans-serif}
.social{left:537px;top:40px;display:flex;gap:6px}
.social span{width:16px;height:16px}
</style>
</head>
<body>

<header class="abs hero">
  <div class="abs hero-photo" role="img" aria-label="Baby back ribs glazed with barbecue sauce on butcher paper over a wooden table"></div>
  <nav>
    <span class="abs nav-item current" style="left:53px">HOME</span>
    <span class="abs nav-item" style="left:89px">NOSOTROS</span>
    <span class="abs nav-item" style="left:144px">MENU</span>
    <span class="abs nav-item" style="left:179px">PROMOCION</span>
    <span class="abs nav-item" style="left:240px">UBICACION</span>
  </nav>
  <div class="abs brand">K&amp;T<br>SMOKEHOUSE</div>
  <a class="abs btn-outline" style="left:446px;width:94px">ORDER ONLINE</a>
  <a class="abs btn-outline" style="left:545px;width:104px">ORDER CATERING</a>
  <h1 class="abs hero-title">RICAS COSTILLITAS BABY BACK DE K&amp;T<br>SMOKEHOUSE ASADERÍA</h1>
  <a class="abs btn-more">VIEW MORE</a>
  <div class="abs dots"><span></span><span class="on"></span><span></span><span></span><span></span></div>
</header>

<section class="abs featured">
  <div class="abs feature-card" style="left:50px"><div class="photo" role="img" aria-label="Rack of smoked ribs" style="background:linear-gradient(160deg,#5a2a1a,#8a4a30 50%,#3a1a10)"></div><div class="label">NUESTRAS COSTILLITAS</div></div>
  <div class="abs feature-card" style="left:254px"><div class="photo" role="img" aria-label="Golden french fries" style="background:linear-gradient(160deg,#c9a26a,#e7c994 50%,#a97a45)"></div><div class="label">PAPAS A LA FRANCESA</div></div>
  <div class="abs feature-card" style="left:457px"><div class="photo" role="img" aria-label="Moonshine jars on a wooden table" style="background:linear-gradient(160deg,#4a3c30,#c9c4bc 50%,#5a1a12)"></div><div class="label">ENSALADA ORGANICA</div></div>
</section>

<section class="abs menu" role="region" aria-label="Menu">
  <h2 class="abs menu-title">MENU</h2>
  <svg class="abs arrow" style="left:24px" width="18" height="36" viewBox="0 0 18 36"><polyline points="16,1 2,18 16,35" fill="none" stroke="#fff" stroke-width="1.2"/></svg>
  <svg class="abs arrow" style="left:659px" width="18" height="36" viewBox="0 0 18 36"><polyline points="2,1 16,18 2,35" fill="none" stroke="#fff" stroke-width="1.2"/></svg>
  <div class="abs dish" style="left:52px"><div class="photo" role="img" aria-label="Glazed ribs" style="background:linear-gradient(150deg,#e8e0dc,#7a2a20 45%,#3a0e0a)"></div><p class="name">SIMPLY DUMMY TEXT</p><p class="price">$115.00</p><a class="order">ORDER NOW</a></div>
  <div class="abs dish" style="left:202px"><div class="photo" role="img" aria-label="Sweet potato fries" style="background:linear-gradient(150deg,#c45a20,#e0874a 50%,#f3e6da)"></div><p class="name">SIMPLY DUMMY TEXT</p><p class="price">$115.00</p><a class="order">ORDER NOW</a></div>
  <div class="abs dish" style="left:353px"><div class="photo" role="img" aria-label="Barbecue ribs close up" style="background:linear-gradient(150deg,#6a1a10,#a8301c 50%,#4a0e08)"></div><p class="name">SIMPLY DUMMY TEXT</p><p class="price">$115.00</p><a class="order">ORDER NOW</a></div>
  <div class="abs dish" style="left:503px"><div class="photo" role="img" aria-label="Cornbread muffins" style="background:linear-gradient(150deg,#3a2a22,#c9a27a 50%,#5a4030)"></div><p class="name">SIMPLY DUMMY TEXT</p><p class="price">$115.00</p><a class="order">ORDER NOW</a></div>
</section>

<h2 class="abs section-title" style="left:52px;top:887px">LATEST NEWS</h2>
<div class="abs news-item" style="top:920px"><div class="date"><b>20</b><i>mar</i></div><h3>NEWS HEADLINE HERE</h3><p>Lorem ipsum dolor sit amet, con-</p></div>
<div class="abs news-rule"></div>
<div class="abs news-item" style="top:980px"><div class="date"><b>20</b><i>mar</i></div><h3>NEWS HEADLINE HERE</h3><p>Lorem ipsum dolor sit amet, con-</p></div>

<h2 class="abs section-title" style="left:230px;top:887px">BLOG</h2>
<article class="abs post" style="left:230px"><div class="photo" role="img" aria-label="Restaurant storefront" style="background:linear-gradient(150deg,#1a1a1a,#7a7a70 50%,#2a2a26)"></div><p>IPSUM IS SIMPLY DUMMY TEXT</p></article>
<article class="abs post" style="left:373px"><div class="photo" role="img" aria-label="Pulled pork sandwich" style="background:linear-gradient(150deg,#d8c8b8,#a04a28 50%,#e8e0d8)"></div><p>IPSUM IS SIMPLY DUMMY TEXT</p></article>
<article class="abs post" style="left:516px"><div class="photo" role="img" aria-label="Sauce bottles beside ribs" style="background:linear-gradient(150deg,#c9a040,#5a3a2a 50%,#3a2a20)"></div><p>IPSUM IS SIMPLY DUMMY TEXT</p></article>

<section class="abs contact">
  <h2 class="abs loc">LOCATIONS</h2>
  <div class="abs select">Select Location
    <svg style="position:absolute;right:10px;top:11px" width="11" height="7" viewBox="0 0 11 7"><polygon points="0,0 11,0 5.5,7" fill="#111"/></svg>
  </div>
  <div class="abs delivery">SERVICIO A DOMICILIO<br>Email: ventas@ktsmokehouse.mx</div>
  <div class="abs phone">
    <svg width="14" height="14" viewBox="0 0 24 24"><path fill="#fff" d="M6.6 10.8a15.1 15.1 0 0 0 6.6 6.6l2.2-2.2c.3-.3.7-.4 1-.2 1.1.4 2.3.6 3.6.6.6 0 1 .4 1 1V20c0 .6-.4 1-1 1A17 17 0 0 1 3 4c0-.6.4-1 1-1h3.5c.6 0 1 .4 1 1 0 1.3.2 2.5.6 3.6.1.3 0 .7-.2 1z"/></svg>
    <span>555 014 2290</span>
  </div>
</section>

<footer class="abs footer">
  <p class="abs links">Privacy Policy | Terms Conditions | Sitemap | Contact Us</p>
  <p class="abs copy">Copyright © 2015&nbsp; All Rights Reserved</p>
  <p class="abs follow">FOLLOW US</p>
  <div class="abs social" aria-label="Social networks">
    <span style="background:#3a9ad9"></span><span style="background:#3b5998"></span><span style="background:#2a3a4a"></span><span style="background:#d01f2f"></span><span style="background:#444"></span>
  </div>
</footer>

</body>
</html>
```